Personal Chef Needs a Good Web Design

Hi everyone!
My name is Leo, I work as a private chef for last 10 years, traveling all around the world and cooking in private megayacht and villas.
I'm about to settle down in my hometown in Europe for a while. And therefore I need a website that will show my story, pics and recipes, nutritional advices and of course offer a Personal and Private Chef services( working for 4-5 families and bringing delicious food to their house).
My clients are extremely rich folks, but usually are down to earth ones.
I believe, the web site should be focused on attention to:
-VIP person's wife( as she is usually responsible for food for family) and be simple.
-to famous people agents and be on high level.

There will be about 10 different menus and 6 different service offers

--UPDATE--
Logo Design:
+My thoughts are- printed structure of the vegetable or fruit on a white font. Like you slice the buffalo tomato, put it in red paint and print it on the edge of the page. See attached files named logo. Can be any nice structured thing, like tomato, lemon, red cabbage etc.
+Classic logos with chef's hat or knives are good too.
+Need to have the space for me to add the name( the fonts can be provided)

Target Market(s)

Private person. 80% Russian clients.

Industry/Entity Type

Cooking

Coding

Coded - Design and coding required

Number of Pages Required

3 page

Requirements
Must have
• Contact form/ Request back call/ Schedule a free consultation
Nice to have
• The client will need to choose straight ahead from the range of services I offer, like:
• -Private Chef( cooking only for the client)
• -Personal Chef( cooking for around 5 clients, bringing the ready to be heated food to their door)
• -Romantic dinner for two
• -Professional Sommelier service
• -Build your kitchen( offering design, equipment and that will fit your requirements)
• -Other( flowers, waiters, barista, equipment rental)
• So this column should go right after the introduction/aboutme part and will lead to separate pages with how-it-works thing for each.

```html
<!DOCTYPE html>
<html lang="en">
<head>
<meta charset="utf-8">
<title>Ember Table – Personal and Private Chef Leo</title>
<link rel="stylesheet" href="https://fonts.googleapis.com/css2?family=Lora:wght@400;700&family=Open+Sans:wght@400;600&display=swap">
<style>
:root{
  --red:#b3132b;
  --ink:#2a2a2a;
  --text:#555;
  --band:#f2f2f2;
  --white:#fff;
}
*{box-sizing:border-box;margin:0;padding:0}
html,body{width:1200px;height:3220px;overflow:hidden}
body{background:var(--white);font-family:"Open Sans",Arial,sans-serif;color:var(--text);font-size:12.5px;line-height:1.75}
h1,h2,h3{font-family:"Lora",Georgia,serif;font-weight:400}
.wrap{width:934px;margin:0 auto;position:relative}

/* hero */
.hero{position:relative;height:615px;background:linear-gradient(100deg,#d9d4cc 0%,#cfc6ba 25%,#e4ded6 55%,#bdb5ab 100%)}
.hero-photo{position:absolute;inset:0}
.topbar{position:absolute;top:0;left:0;right:0;height:80px;background:rgba(20,20,20,.88)}
.topbar .wrap{height:80px;display:flex;align-items:center;justify-content:space-between}
.brand{font-family:"Lora",Georgia,serif;color:var(--white);font-size:34px;line-height:1}
.nav{display:flex;gap:28px}
.nav a{color:#e6e6e6;text-decoration:none;font-size:12.5px}
.nav a.current{text-decoration:underline;text-underline-offset:4px}
.slide-arrow{position:absolute;top:330px;width:26px;height:32px;background:rgba(150,150,150,.75);display:flex;align-items:center;justify-content:center}
.slide-arrow.prev{left:0}.slide-arrow.next{right:0}
.booking{position:absolute;left:653px;top:176px;width:413px;height:344px;background:rgba(255,255,255,.78);padding:22px 18px;text-align:center}
.booking h2{color:var(--red);font-size:21px;line-height:1.3}
.booking p{font-size:11px;line-height:1.5;color:#333;margin:8px 30px 12px}
.fields{display:grid;grid-template-columns:1fr 1fr;gap:10px 12px}
.field{height:38px;border:2px solid #555;display:flex;align-items:center;justify-content:space-between;padding:0 12px;font-size:11px;color:#333;text-transform:uppercase}
.book-btn{display:inline-block;margin-top:18px;background:#2b2b2b;color:var(--white);font-size:14px;padding:9px 16px;text-transform:uppercase}

/* welcome */
.welcome{height:338px;padding-top:72px;text-align:center}
.title{color:var(--red);font-size:34px;line-height:1.2}
.welcome .title{margin-bottom:18px}
.welcome p{margin-bottom:18px}

/* split bands */
.band{background:var(--band)}
.story{height:277px;padding-top:47px}
.split{display:flex;gap:22px;align-items:flex-start}
.split .copy-col{flex:1;min-width:0}
.split h3{color:var(--red);font-size:21px;line-height:1.2;margin:5px 0 10px}
.photo{display:block;flex:none}
.media{width:280px;height:182px}
.btn{display:inline-block;border:1px solid #999;background:var(--white);color:#333;font-size:11px;padding:9px 16px;margin-top:14px}
.play{position:relative}
.play svg{position:absolute;left:50%;top:50%;transform:translate(-50%,-50%)}

/* services */
.services{height:518px;padding-top:72px;text-align:center}
.services p{margin:14px 0 26px}
.grid3{display:flex;justify-content:space-between}
.grid3 > .photo{width:297px;height:192px}
.dots{display:flex;justify-content:center;gap:14px;margin-top:30px}
.dots i{width:8px;height:8px;border-radius:50%;background:#c9c9c9}
.dots i.on{background:var(--red)}

.nutrition{height:275px;padding-top:45px}

/* recipes */
.recipes{height:513px;padding-top:72px}
.head-row{display:flex;justify-content:space-between;align-items:center;margin-bottom:22px}
.arrows{display:flex;gap:6px}
.arrows span{width:23px;height:23px;border:1px solid #888;display:flex;align-items:center;justify-content:center}
.card{width:297px}
.card .photo{height:192px}
.card h3{color:var(--ink);font-size:17px;line-height:1.3;margin-top:12px}

/* menu */
.menu{height:484px;background:#f7f7f7;padding-top:42px;text-align:center}
.menu .title{color:#a9a9a9}
.tabs{font-family:"Lora",Georgia,serif;font-size:21px;color:#777;margin:6px 0 18px}
.tabs .on{color:var(--red);border-bottom:2px solid var(--red)}
.tabs b{font-weight:400;margin:0 12px}
.menu .card h3{font-size:16px;text-align:center}

/* footer */
.footer{height:125px;background:#f0f0f0;border-top:1px solid #e2e2e2;padding-top:28px;font-size:11px;color:#444}
.footer .wrap{display:flex}
.links{list-style:none;line-height:2.15}
.links li::before{content:"•";margin-right:6px;color:#777}
.col1{width:135px}.col2{width:145px}.col3{width:205px}
.contact{list-style:none;line-height:2.15;width:360px}
.contact li{display:flex;align-items:center;gap:10px}
.social{display:grid;grid-template-columns:repeat(3,28px);gap:4px;margin-left:auto;margin-right:48px;align-content:start}
.social span{width:26px;height:26px;border-radius:50%;background:#2c3e67}
.copyright{height:75px;display:flex;align-items:center;justify-content:center;font-size:11px;color:#444}
</style>
</head>
<body>

<header class="hero">
  <div class="hero-photo" role="img" aria-label="Smiling chef in white jacket and tall hat holding a wooden spoon in a blurred professional kitchen"></div>
  <div class="topbar">
    <div class="wrap">
      <div class="brand">Ember Table</div>
      <nav class="nav">
        <a class="current">Home</a><a>My Story</a><a>Services</a><a>Menu</a><a>Gallery</a><a>Recipes</a><a>Nutritional Advices</a><a>Contact</a>
      </nav>
    </div>
  </div>
  <span class="slide-arrow prev"><svg width="8" height="12" viewBox="0 0 8 12"><path d="M7 1 2 6l5 5" fill="none" stroke="#fff" stroke-width="1.6"/></svg></span>
  <span class="slide-arrow next"><svg width="8" height="12" viewBox="0 0 8 12"><path d="m1 1 5 5-5 5" fill="none" stroke="#fff" stroke-width="1.6"/></svg></span>

  <form class="booking">
    <h2>Maecenas imperdiet aliquet diam, a porttitor risus</h2>
    <p>Integer ut diam id magna efficitur placerat et eu quam. Duis tellus est, condimentum a volutpat sit amet.</p>
    <div class="fields">
      <div class="field">Name</div>
      <div class="field">Email</div>
      <div class="field">Phone</div>
      <div class="field">Date <svg width="12" height="12" viewBox="0 0 12 12"><rect x="1" y="2" width="10" height="9" fill="none" stroke="#333"/><path d="M1 5h10M4 1v2M8 1v2" stroke="#333"/></svg></div>
      <div class="field">Location <svg width="10" height="13" viewBox="0 0 10 13"><path d="M5 12S1 7.5 1 5a4 4 0 0 1 8 0c0 2.5-4 7-4 7z" fill="none" stroke="#333"/><circle cx="5" cy="5" r="1.4" fill="#333"/></svg></div>
      <div class="field">Cuisine <svg width="9" height="6" viewBox="0 0 9 6"><path d="m1 1 3.5 3.5L8 1" fill="none" stroke="#333"/></svg></div>
    </div>
    <span class="book-btn">Book now</span>
  </form>
</header>

<section class="welcome">
  <div class="wrap">
    <h1 class="title">Welcome</h1>
    <p>Our first consultation will be in your home. We will discuss any food preferences you may have, as well as any allergy or dietary needs. At this time we will also discuss what kind of meals you like, from meat and potatoes to all organic, vegan and vegetarian meals or international cuisine like Italian or Mexican . If you have concerns about your diet we can work with any restrictions you have.</p>
    <p>On your scheduled cook date: We will prepare your meals in our commercial kitchen and drop them off to you at your convenience. Your meals will be chilled, packaged, labeled and stored in your refrigerator or freezer with easy instructions for heating. Meals can be packaged in single servings or family style. All meals will have special heating instructions which most only require you heating it up in the oven.</p>
  </div>
</section>

<section class="band story">
  <div class="wrap split">
    <div class="photo media play" style="background:linear-gradient(135deg,#6b4a2c,#c9a57a 55%,#8a6a48)" role="img" aria-label="Plated dish on a restaurant table with wine glasses, video">
      <svg width="40" height="40" viewBox="0 0 40 40"><circle cx="20" cy="20" r="19" fill="#fff"/><path d="M16 12v16l12-8z" fill="#222"/></svg>
    </div>
    <div class="copy-col">
      <h3>My Story</h3>
      <p>Nam hendrerit nisi vel suscipit tincidunt. Sed et sagittis nibh. Suspendisse eget nunc fringilla, viverra lorem pellentesque, gravida justo. Vestibulum massa velit, malesuada eu condimentum eu, sagittis eget diam. Etiam sagittis felis in orci feugiat bibendum. Vestibulum laoreet, elit quis congue venenatis, nibh ipsum ultricies lectus, at congue ante tortor vel ipsum. Sed orci libero, tristique et dapibus nec, blandit in sem. Suspendisse blandit ex id posuere interdum. Curabitur nulla risus, elementum at tristique at, consectetur at justo. Sed efficitur, erat quis aliquam vulputate.</p>
      <span class="btn">Read more</span>
    </div>
  </div>
</section>

<section class="services">
  <div class="wrap">
    <h2 class="title">Personal and Private Chef Services</h2>
    <p>Duis quis tincidunt quam. Mauris euismod ipsum sodales sapien mattis luctus. Phasellus ultricies metus id iaculis mattis. Nullam malesuada auctor tincidunt. Sed nec tristique leo. Phasellus finibus, quam ut mattis scelerisque, est augue molestie ipsum, consequat porta leo quam et lectus. Nam tincidunt eros in tellus sollicitudin, non semper turpis pellentesque. In hac habitasse platea dictumst.</p>
    <div class="grid3">
      <div class="photo" style="background:linear-gradient(160deg,#2b2622,#5a4a3e 60%,#1c1815)" role="img" aria-label="Chef drizzling sauce over a plated dish"></div>
      <div class="photo" style="background:linear-gradient(160deg,#1f2326,#4f5a60 55%,#2a2e30)" role="img" aria-label="Chef garnishing a plate with tweezers"></div>
      <div class="photo" style="background:linear-gradient(160deg,#2a2420,#6b4f3a 55%,#c8b9a8)" role="img" aria-label="Chef finishing a plated dish beside a copper pot"></div>
    </div>
    <div class="dots"><i class="on"></i><i></i><i></i><i></i></div>
  </div>
</section>

<section class="band nutrition">
  <div class="wrap split">
    <div class="copy-col">
      <h3>Nutritional Advices</h3>
      <p>Nam hendrerit nisi vel suscipit tincidunt. Sed et sagittis nibh. Suspendisse eget nunc fringilla, viverra lorem pellentesque, gravida justo. Vestibulum massa velit, malesuada eu condimentum eu, sagittis eget diam. Etiam sagittis felis in orci feugiat bibendum. Vestibulum laoreet, elit quis congue venenatis, nibh ipsum ultricies lectus, at congue ante tortor vel ipsum. Sed orci libero, tristique et dapibus nec, blandit in sem. Suspendisse blandit ex id posuere interdum. Curabitur nulla risus, elementum at tristique at, consectetur at justo. Sed efficitur, erat quis aliquam vulputate.</p>
      <span class="btn">View all</span>
    </div>
    <div class="photo media play" style="margin-left:40px;background:linear-gradient(135deg,#c7d3dc,#e8c9a0 50%,#7fae4a)" role="img" aria-label="Person choosing between fresh fruit and vegetables, video">
      <svg width="40" height="40" viewBox="0 0 40 40"><circle cx="20" cy="20" r="19" fill="#fff"/><path d="M16 12v16l12-8z" fill="#222"/></svg>
    </div>
  </div>
</section>

<section class="recipes">
  <div class="wrap">
    <div class="head-row">
      <h2 class="title">Recipes</h2>
      <div class="arrows">
        <span><svg width="6" height="10" viewBox="0 0 6 10"><path d="M5 1 1 5l4 4" fill="none" stroke="#333"/></svg></span>
        <span><svg width="6" height="10" viewBox="0 0 6 10"><path d="m1 1 4 4-4 4" fill="none" stroke="#333"/></svg></span>
      </div>
    </div>
    <div class="grid3">
      <div class="card">
        <div class="photo" style="background:linear-gradient(150deg,#7a3a14,#b8733c 50%,#e9e2d8)" role="img" aria-label="Seared meat pieces on a white plate"></div>
        <h3>Duis condimentum eu justo elementum egestas et non tellus</h3>
        <span class="btn">Read more</span>
      </div>
      <div class="card">
        <div class="photo" style="background:linear-gradient(150deg,#8e8a80,#d9b46a 50%,#7a5a38)" role="img" aria-label="Soft tacos filled with meat and greens"></div>
        <h3>Duis condimentum eu justo elementum egestas et non tellus</h3>
        <span class="btn">Read more</span>
      </div>
      <div class="card">
        <div class="photo" style="background:linear-gradient(150deg,#8a5a34,#b8462c 50%,#6e4a2c)" role="img" aria-label="Grilled fish with tomatoes and lemon"></div>
        <h3>Duis condimentum eu justo elementum egestas et non tellus</h3>
        <span class="btn">Read more</span>
      </div>
    </div>
  </div>
</section>

<section class="menu">
  <div class="wrap">
    <h2 class="title">Menu</h2>
    <div class="tabs"><span class="on">Seafood</span><b>|</b>Chicken<b>|</b>Beef<b>|</b>Pork</div>
    <div class="grid3">
      <div class="card">
        <div class="photo" style="background:linear-gradient(150deg,#6a8a3a,#b5632a 45%,#3a3a3a)" role="img" aria-label="Glazed fish strips on a plate with salad"></div>
        <h3>Thai Style Mahi with a Coconut Coucous</h3>
      </div>
      <div class="card">
        <div class="photo" style="background:linear-gradient(150deg,#e6a34a,#efe6d4 55%,#cfc8b8)" role="img" aria-label="Herb crusted fish fillet with citrus slices"></div>
        <h3>Garlic and Herb Crusted Seabass</h3>
      </div>
      <div class="card">
        <div class="photo" style="background:linear-gradient(150deg,#2a1d16,#6a4a34 40%,#e9e4dc)" role="img" aria-label="Poached fish on a bed of rice"></div>
        <h3>Poached Halibut with Leeks and Grape Tomatoes</h3>
      </div>
    </div>
    <div class="dots"><i class="on"></i><i></i><i></i><i></i></div>
  </div>
</section>

<footer>
  <div class="footer">
    <div class="wrap">
      <ul class="links col1"><li>Home</li><li>My Story</li><li>Services</li></ul>
      <ul class="links col2"><li>Menu</li><li>Gallery</li><li>Recipes</li></ul>
      <ul class="links col3"><li>Nutritional Advices</li><li>Contact</li><li>Sitemap</li></ul>
      <ul class="contact">
        <li><svg width="9" height="12" viewBox="0 0 10 13"><path d="M5 12S1 7.5 1 5a4 4 0 0 1 8 0c0 2.5-4 7-4 7z" fill="#333"/><circle cx="5" cy="5" r="1.4" fill="#fff"/></svg>24 Building name, Street name, City - Zipcode</li>
        <li><svg width="8" height="12" viewBox="0 0 8 12"><rect x="0.5" y="0.5" width="7" height="11" rx="1" fill="#333"/><rect x="1.8" y="2" width="4.4" height="7" fill="#fff"/></svg>465 300 0172</li>
        <li><svg width="11" height="8" viewBox="0 0 11 8"><rect width="11" height="8" fill="#333"/><path d="m0 0 5.5 4.5L11 0" fill="none" stroke="#fff"/></svg>hello@embertable.com</li>
      </ul>
      <div class="social" aria-label="Social links">
        <span></span><span></span><span></span><span></span><span></span>
      </div>
    </div>
  </div>
  <div class="copyright">Copyright © 2016 Company name. All rights reserved.</div>
</footer>

</body>
</html>
```